Website mockup using figma or other design software for Plumbing Company

We are looking for a talented UI/UX designer to create a high-converting, modern, and professional website design for a local plumbing company. The goal is to move away from the "dated" look of traditional trades and provide a seamless, trustworthy experience for homeowners and commercial clients.
The Challenge
Create a Homepage and a Service Page design that balances professional expertise with an urgent "call-to-action" (CTA) focus. We need a design that looks great on desktop but is built with a mobile-first mindset, as most customers find plumbers via their phones during emergencies.
This company will focus more on B2B, and corporate contracts, but should still be friendly to the public.
Here are some examples of what we are looking for
https://velotrin-works.com/construction/plumbing-construction/
https://velotrin-works.com/
The company is called "KT Plumbing."
Please see the logo below.

```html
<!DOCTYPE html>
<html lang="en">
<head>
<meta charset="utf-8">
<title>Velotrin Works — MEP Expertise</title>
<link href="https://fonts.googleapis.com/css2?family=Red+Hat+Display:ital,wght@0,400;0,500;0,600;0,700;0,800;1,400&display=swap" rel="stylesheet">
<style>
:root{
  --orange:#ff4f12;
  --navy:#0d1b29;
  --navy-2:#1b2d3d;
  --ink:#1a1a1a;
  --muted:#6b6b6b;
  --white:#ffffff;
  --line:#e6e6e6;
}
*{box-sizing:border-box;margin:0;padding:0}
html,body{width:1200px;height:4068px;overflow:hidden}
body{font-family:"Red Hat Display",Arial,sans-serif;color:var(--ink);background:var(--white);position:relative}
.abs{position:absolute}
.ph{position:absolute}

/* header / hero */
.hero{position:absolute;left:0;top:0;width:1200px;height:595px;background:linear-gradient(90deg,#050505 0%,#17120f 45%,#4a3324 70%,#8a4a22 85%,#3a2a20 100%)}
.hero .ph{left:520px;top:0;width:680px;height:595px;background:radial-gradient(circle at 65% 45%,rgba(255,110,30,.55),rgba(90,60,40,.35) 45%,rgba(0,0,0,0) 75%)}
.brand{position:absolute;display:flex;align-items:center;gap:10px;color:var(--white);font-weight:800;letter-spacing:.5px}
.brand .mark{width:22px;height:22px;background:var(--white)}
.hero .brand{left:150px;top:32px;font-size:26px}
.nav{position:absolute;left:482px;top:40px;display:flex;gap:31px;font-size:12.5px;font-weight:600;color:var(--white);letter-spacing:.2px}
.hero-title{position:absolute;left:150px;top:210px;border-left:4px solid var(--orange);padding-left:20px;color:var(--white);font-size:35px;line-height:46px;font-weight:800}
.hero-title .light{font-weight:400}
.skew-btn{position:absolute;height:44px;display:flex;align-items:center;justify-content:center;gap:12px;font-size:15px;font-weight:700;color:var(--white)}
.skew-btn::before{content:"";position:absolute;inset:0;transform:skewX(-28deg);z-index:-1}
.skew-btn.outline::before{border:2px solid var(--white)}
.skew-btn.solid::before{background:var(--navy)}
.hero .skew-btn{z-index:1}
.arrow{width:16px;height:10px}

/* section heads */
.eyebrow{position:absolute;left:0;width:1200px;text-align:center;font-size:19px;font-weight:500;letter-spacing:.5px}
.sec-title{position:absolute;left:0;width:1200px;text-align:center;font-size:35px;font-weight:700;letter-spacing:.5px}
.divider{position:absolute;display:flex;gap:14px;align-items:center}
.divider i{display:block;height:3px;background:var(--orange);width:80px}
.divider b{display:block;height:3px;background:var(--navy);width:20px}

/* about */
.about-img{left:150px;top:710px;width:392px;height:438px;background:linear-gradient(180deg,#7fa7c9 0%,#b9c7cf 28%,#b59a74 45%,#8a6f52 100%)}
.stripes{position:absolute;width:110px;height:110px}
.about-eyebrow{left:612px;top:744px;font-size:19px;font-weight:500}
.about-title{left:608px;top:780px;font-size:35px;font-weight:700}
.about-text{left:612px;top:862px;width:412px;font-size:14.5px;line-height:25.6px;color:var(--muted);text-align:justify}

/* services */
.card-img{position:absolute;top:1413px;width:286px;height:295px}
.card-label{position:absolute;top:1678px;width:236px;height:59px;display:flex;align-items:center;justify-content:center;color:var(--white);font-size:15px;font-weight:700;background:var(--navy)}
.card-label.active{background:var(--orange)}

/* why */
.why{position:absolute;left:0;top:1852px;width:1200px;height:591px;background:var(--navy-2)}
.why .eyebrow,.why .sec-title{color:var(--white)}
.why-item{position:absolute;width:260px;color:var(--white)}
.why-item h4{font-size:14px;font-weight:700;margin-bottom:6px}
.why-item p{font-size:11px;line-height:18px;font-weight:600}
.why-item.left{text-align:right}
.why-icon{position:absolute;width:68px;height:68px;border-radius:50%;border:3px solid var(--white);background:#eef1f4;display:flex;align-items:center;justify-content:center}
.why-person{left:497px;top:2060px;width:229px;height:383px;background:linear-gradient(180deg,#c9a287 0%,#d9d9d9 35%,#22304a 60%,#c2923f 80%,#22304a 100%);border-radius:110px 110px 0 0}

/* testimonials */
.review{position:absolute;top:2676px;width:264px;height:250px;border:1px solid var(--line);background:var(--white);padding:18px 18px}
.review .avatar{width:64px;height:64px;border-radius:50%;border:3px solid var(--orange);background:linear-gradient(180deg,#8a9ba8,#3b4652)}
.review .name{position:absolute;left:96px;top:30px;font-size:15px;font-weight:600}
.review .date{position:absolute;left:96px;top:52px;font-size:11px;color:var(--muted)}
.review p{margin-top:24px;font-size:11.5px;line-height:21px;font-style:italic;color:var(--muted)}

/* capabilities */
.cap-title{left:161px;top:3076px;font-size:35px;font-weight:700}
.cap-lead{left:164px;top:3128px;width:420px;font-size:15px;line-height:25px;font-weight:500}
.cap-list{position:absolute;left:164px;top:3214px;list-style:none}
.cap-list li{display:flex;align-items:center;gap:18px;font-size:15px;height:26.3px;color:#333}
.cap-img{left:650px;top:3047px;width:394px;height:438px;background:radial-gradient(circle at 55% 25%,#f0f0f0 0 10%,#e2512a 11% 22%,#6b3a30 35%,#c9a08a 60%,#8d8d8d 100%)}

/* footer */
.footer{position:absolute;left:0;top:3652px;width:1200px;height:416px;background:var(--navy);color:var(--white)}
.footer .brand{left:175px;top:125px;font-size:30px}
.socials{position:absolute;left:194px;top:216px;display:flex;gap:28px}
.socials span{width:16px;height:16px;border-radius:50%;border:2px solid var(--white)}
.fcol{position:absolute;top:88px;font-size:12.5px}
.fcol h5{font-size:18px;font-weight:600;margin-bottom:4px}
.fcol .u{display:block;width:26px;height:3px;background:var(--white);margin-bottom:14px}
.fcol a{display:block;color:var(--white);text-decoration:none;line-height:26.5px}
.fcol .lbl{font-size:11px;opacity:.85;margin-bottom:2px}
.fcol .val{line-height:20px;margin-bottom:14px;display:flex;gap:6px;align-items:flex-start}
.news-field{position:absolute;left:808px;top:222px;width:242px;height:34px;border-radius:17px;background:var(--white);color:#333;font-size:11px;display:flex;align-items:center;padding-left:16px}
.news-field .send{position:absolute;right:8px;top:8px;width:18px;height:18px;border-radius:50%;background:var(--navy)}
.f-rule{position:absolute;left:175px;top:310px;width:856px;height:1px;background:rgba(255,255,255,.55)}
.copy{position:absolute;left:0;top:345px;width:1200px;text-align:center;font-size:13px;font-weight:600}
</style>
</head>
<body>

<header class="hero">
  <div class="ph" role="img" aria-label="Photo of a plumber in an orange jacket and safety glasses working with a pipe wrench"></div>
  <div class="brand"><span class="mark"></span>VELOTRIN</div>
  <nav class="nav"><span>VW SERVICE</span><span>VW MEP</span><span>PROJECTS</span><span>CAREERS</span><span>ABOUT</span><span>BLOG</span><span>CONTACT</span></nav>
  <h1 class="hero-title">PROVIDING<br><span class="light">MEP EXPERTISE</span> FROM<br>CONCEPT TO MAINTENANCE</h1>
  <a class="skew-btn outline" style="left:160px;top:358px;width:168px">VW MEP <svg class="arrow" viewBox="0 0 16 10"><path d="M0 5h13M9 1l4 4-4 4" stroke="#fff" stroke-width="2" fill="none"/></svg></a>
  <a class="skew-btn outline" style="left:340px;top:358px;width:170px">VW SERVICE <svg class="arrow" viewBox="0 0 16 10"><path d="M0 5h13M9 1l4 4-4 4" stroke="#fff" stroke-width="2" fill="none"/></svg></a>
</header>

<section class="about">
  <svg class="stripes" style="left:98px;top:1085px" viewBox="0 0 110 110"><g fill="#0d1b29"><polygon points="40,0 54,0 14,100 0,100"/><polygon points="62,0 76,0 36,100 22,100"/><polygon points="84,0 98,0 58,100 44,100"/></g></svg>
  <div class="ph about-img" role="img" aria-label="Photo of capped white PVC pipes rising from a graded dirt site with a compact loader behind"></div>
  <div class="abs about-eyebrow">ABOUT</div>
  <h2 class="abs about-title">VELOTRIN WORKS</h2>
  <div class="divider" style="left:610px;top:836px"><i></i><b></b></div>
  <p class="abs about-text">Velotrin takes a big-picture approach to the construction process by self-performing electrical, HVAC, plumbing, process piping, underground utilities, prefabrication, and MEP design. Instead of multiple consultants and countless subcontractors, our customers work with just one company to eliminate profit layers, scope gaps, and complexity of schedules.</p>
  <a class="skew-btn solid" style="left:624px;top:1075px;width:218px">MORE ABOUT US <svg class="arrow" viewBox="0 0 16 10"><path d="M0 5h13M9 1l4 4-4 4" stroke="#fff" stroke-width="2" fill="none"/></svg></a>
</section>

<section class="services">
  <div class="eyebrow" style="top:1276px">SERVICES</div>
  <h2 class="sec-title" style="top:1316px">PROFESSIONAL PLUMBING</h2>
  <div class="divider" style="left:547px;top:1377px"><i></i><b></b></div>
  <div class="card-img" style="left:150px;background:linear-gradient(160deg,#6d7b86,#3f4b55 60%,#7a6a55)" role="img" aria-label="Photo of a plumber repairing a drain pipe under a sink"></div>
  <div class="card-img" style="left:458px;background:linear-gradient(180deg,#e9ecef,#cfd5da 50%,#2d4f8c 75%,#e5e8ea)" role="img" aria-label="Photo of a technician servicing wall-mounted water heaters"></div>
  <div class="card-img" style="left:764px;background:linear-gradient(160deg,#f2f2f2,#d8dadc 45%,#3b6bb0 70%,#c93b33 90%)" role="img" aria-label="Photo of a plumber using a drain snake under a kitchen cabinet"></div>
  <div class="card-label" style="left:172px">EMERGENCY PLUMBING</div>
  <div class="card-label active" style="left:480px">COMMERCIAL PLUMBING</div>
  <div class="card-label" style="left:787px">DRAIN CLEANING</div>
</section>

<section>
  <svg class="abs" style="left:0;top:1852px" width="1200" height="84" viewBox="0 0 1200 84"><polygon points="0,84 600,0 1200,84" fill="#1b2d3d"/></svg>
  <div class="why" style="top:1934px;height:509px"></div>
  <div class="eyebrow" style="top:1925px;color:#fff;font-weight:700">VELOTRIN</div>
  <h2 class="sec-title" style="top:1966px;color:#fff">WHY CHOOSE US</h2>
  <div class="divider" style="left:547px;top:2025px"><i></i><b style="background:#fff"></b></div>

  <div class="why-item left" style="left:123px;top:2094px"><h4>Licensed Master Plumbers</h4><p>Nemo enim ipsam voluptatem quia voluptas sit aspernatur aut odit aut</p></div>
  <div class="why-item left" style="left:123px;top:2196px"><h4>Fast Dispatch</h4><p>Nemo enim ipsam voluptatem quia voluptas sit aspernatur aut odit aut</p></div>
  <div class="why-item left" style="left:123px;top:2292px"><h4>Upfront Pricing</h4><p>Nemo enim ipsam voluptatem quia voluptas sit aspernatur aut odit aut</p></div>
  <div class="why-item" style="left:818px;top:2094px"><h4>Modern Equipment</h4><p>Nemo enim ipsam voluptatem quia voluptas sit aspernatur aut odit aut</p></div>
  <div class="why-item" style="left:818px;top:2196px"><h4>Preventative Maintenance Plans</h4><p>Nemo enim ipsam voluptatem quia voluptas sit aspernatur aut odit aut</p></div>
  <div class="why-item" style="left:818px;top:2292px"><h4>Commercial Contracts</h4><p>Nemo enim ipsam voluptatem quia voluptas sit aspernatur aut odit aut</p></div>

  <div class="why-icon" style="left:420px;top:2088px"><svg width="30" height="30" viewBox="0 0 30 30"><rect x="6" y="3" width="18" height="24" rx="2" fill="none" stroke="#ff4f12" stroke-width="2"/><path d="M10 10h10M10 15h10M10 20h6" stroke="#ff4f12" stroke-width="2"/></svg></div>
  <div class="why-icon" style="left:420px;top:2190px"><svg width="30" height="30" viewBox="0 0 30 30"><rect x="3" y="9" width="16" height="12" fill="none" stroke="#ff4f12" stroke-width="2"/><path d="M19 13h5l3 4v4h-8" fill="none" stroke="#ff4f12" stroke-width="2"/><circle cx="9" cy="23" r="2.5" fill="#ff4f12"/><circle cx="22" cy="23" r="2.5" fill="#ff4f12"/></svg></div>
  <div class="why-icon" style="left:420px;top:2286px"><svg width="30" height="30" viewBox="0 0 30 30"><circle cx="15" cy="15" r="11" fill="none" stroke="#ff4f12" stroke-width="2"/><path d="M15 8v14M11 12h6M13 18h6" stroke="#ff4f12" stroke-width="2"/></svg></div>
  <div class="why-icon" style="left:728px;top:2088px"><svg width="30" height="30" viewBox="0 0 30 30"><rect x="4" y="5" width="22" height="16" rx="2" fill="none" stroke="#ff4f12" stroke-width="2"/><path d="M11 26h8M15 21v5" stroke="#ff4f12" stroke-width="2"/></svg></div>
  <div class="why-icon" style="left:728px;top:2190px"><svg width="30" height="30" viewBox="0 0 30 30"><rect x="6" y="3" width="18" height="24" rx="2" fill="none" stroke="#ff4f12" stroke-width="2"/><path d="M10 15l4 4 7-8" stroke="#ff4f12" stroke-width="2" fill="none"/></svg></div>
  <div class="why-icon" style="left:728px;top:2286px"><svg width="30" height="30" viewBox="0 0 30 30"><path d="M5 25h20M8 22V14M13 22V9M18 22V12M23 22V6" stroke="#ff4f12" stroke-width="2"/></svg></div>
  <div class="ph why-person" role="img" aria-label="Photo of a smiling plumber in overalls holding a pipe wrench and giving a thumbs up"></div>
</section>

<section>
  <div class="eyebrow" style="top:2525px">REVIEWS</div>
  <h2 class="sec-title" style="top:2563px">TESTIMONIALS</h2>
  <div class="divider" style="left:547px;top:2618px"><i></i><b></b></div>
  <article class="review" style="left:150px"><div class="avatar" role="img" aria-label="Reviewer portrait"></div><div class="name">RONAN VESK</div><div class="date">01 Oct 2025</div><p>Sed ut perspiciatis unde omnis iste natus error sit voluptatem accusantium doloremque laudantium, totam rem aperiam, eaque ipsa quae ab illo inventore veritatis et quasi architecto beatae vitae dicta sunt explicabo.</p></article>
  <article class="review" style="left:468px"><div class="avatar" role="img" aria-label="Reviewer portrait"></div><div class="name">RONAN VESK</div><div class="date">01 Oct 2025</div><p>Sed ut perspiciatis unde omnis iste natus error sit voluptatem accusantium doloremque laudantium, totam rem aperiam, eaque ipsa quae ab illo inventore veritatis et quasi architecto beatae vitae dicta sunt explicabo.</p></article>
  <article class="review" style="left:786px"><div class="avatar" role="img" aria-label="Reviewer portrait"></div><div class="name">RONAN VESK</div><div class="date">01 Oct 2025</div><p>Sed ut perspiciatis unde omnis iste natus error sit voluptatem accusantium doloremque laudantium, totam rem aperiam, eaque ipsa quae ab illo inventore veritatis et quasi architecto beatae vitae dicta sunt explicabo.</p></article>
</section>

<section>
  <h2 class="abs cap-title">CAPABILITES</h2>
  <p class="abs cap-lead">Velotrin can design, fabricate, and install any plumbing project need for our customers including:</p>
  <div class="divider" style="left:164px;top:3190px"><i></i><b></b></div>
  <ul class="cap-list">
    <li><svg width="14" height="14" viewBox="0 0 14 14"><circle cx="7" cy="7" r="7" fill="#ff4f12"/><path d="M3.8 7.2l2.2 2.2 4.2-4.4" stroke="#fff" stroke-width="1.8" fill="none"/></svg>Medical gas systems</li>
    <li><svg width="14" height="14" viewBox="0 0 14 14"><circle cx="7" cy="7" r="7" fill="#ff4f12"/><path d="M3.8 7.2l2.2 2.2 4.2-4.4" stroke="#fff" stroke-width="1.8" fill="none"/></svg>Laboratory air &amp; gas systems</li>
    <li><svg width="14" height="14" viewBox="0 0 14 14"><circle cx="7" cy="7" r="7" fill="#ff4f12"/><path d="M3.8 7.2l2.2 2.2 4.2-4.4" stroke="#fff" stroke-width="1.8" fill="none"/></svg>Deionized water systems</li>
    <li><svg width="14" height="14" viewBox="0 0 14 14"><circle cx="7" cy="7" r="7" fill="#ff4f12"/><path d="M3.8 7.2l2.2 2.2 4.2-4.4" stroke="#fff" stroke-width="1.8" fill="none"/></svg>Process plumbing systems</li>
    <li><svg width="14" height="14" viewBox="0 0 14 14"><circle cx="7" cy="7" r="7" fill="#ff4f12"/><path d="M3.8 7.2l2.2 2.2 4.2-4.4" stroke="#fff" stroke-width="1.8" fill="none"/></svg>Fuel oil systems</li>
    <li><svg width="14" height="14" viewBox="0 0 14 14"><circle cx="7" cy="7" r="7" fill="#ff4f12"/><path d="M3.8 7.2l2.2 2.2 4.2-4.4" stroke="#fff" stroke-width="1.8" fill="none"/></svg>Site utilities</li>
    <li><svg width="14" height="14" viewBox="0 0 14 14"><circle cx="7" cy="7" r="7" fill="#ff4f12"/><path d="M3.8 7.2l2.2 2.2 4.2-4.4" stroke="#fff" stroke-width="1.8" fill="none"/></svg>Commercial kitchens</li>
  </ul>
  <a class="skew-btn solid" style="left:175px;top:3418px;width:210px">READ MORE <svg class="arrow" viewBox="0 0 16 10"><path d="M0 5h13M9 1l4 4-4 4" stroke="#fff" stroke-width="2" fill="none"/></svg></a>
  <svg class="stripes" style="left:600px;top:3422px" viewBox="0 0 110 110"><g fill="#0d1b29"><polygon points="40,0 54,0 14,100 0,100"/><polygon points="62,0 76,0 36,100 22,100"/><polygon points="84,0 98,0 58,100 44,100"/></g></svg>
  <div class="ph cap-img" role="img" aria-label="Overhead photo of a worker in a white hard hat and orange shirt fitting copper pipes"></div>
</section>

<footer class="footer">
  <div class="brand"><span class="mark"></span>VELOTRIN</div>
  <div class="socials" aria-label="Social links"><span></span><span></span><span></span><span></span><span></span></div>
  <div class="fcol" style="left:469px"><h5>More Info</h5><span class="u"></span><a>VW Service</a><a>VW MEP</a><a>Projects</a><a>Careers</a><a>About</a></div>
  <div class="fcol" style="left:617px;top:86px;width:170px"><h5>Contact Us</h5><span class="u"></span>
    <div class="lbl">ADDRESS</div>
    <div class="val"><svg width="10" height="13" viewBox="0 0 10 13" style="margin-top:3px;flex:none"><path d="M5 0a5 5 0 0 1 5 5c0 3.5-5 8-5 8S0 8.5 0 5a5 5 0 0 1 5-5z" fill="#fff"/><circle cx="5" cy="5" r="1.8" fill="#0d1b29"/></svg><span>2280 Halden Creek Road<br>Marlow, CA 95190</span></div>
    <div class="lbl">PHONE</div>
    <div class="val"><svg width="12" height="12" viewBox="0 0 12 12" style="margin-top:3px"><path d="M2 0l2.5 3-1.3 1.6a7 7 0 0 0 4.2 4.2L9 7.5 12 10l-1.5 2C5 12 0 7 0 1.5z" fill="#fff"/></svg><span>555-204-7316</span></div>
    <div class="lbl">EMAIL</div>
    <div class="val"><svg width="13" height="10" viewBox="0 0 13 10" style="margin-top:4px"><rect width="13" height="10" fill="#fff"/><path d="M0 0l6.5 5L13 0" stroke="#0d1b29" fill="none"/></svg><span>hello@velotrinworks.com</span></div>
  </div>
  <div class="fcol" style="left:810px;top:86px;width:240px"><h5>Newsletter</h5><span class="u"></span><p style="line-height:20px">Lorem ipsum dolor sit amet, consectetur adipiscing elit, sed do eiusmod tempor</p></div>
  <div class="news-field">Enter Email<span class="send"></span></div>
  <div class="f-rule"></div>
  <div class="copy">© copyrights 2026 &nbsp;Velotrin Works I Rights Reserved</div>
</footer>

</body>
</html>
```